Tall Fern Roofing Business Card

Need a business card with the logo that was designed here

Contact Information for Business Card

Name, Title, Phone, Email, Website, Company name

```html
<!DOCTYPE html>
<html lang="en">
<head>
<meta charset="UTF-8">
<title>Tall Fern Roofing – Business Card</title>
<link href="https://fonts.googleapis.com/css2?family=Montserrat:wght@600;700&family=Open+Sans:wght@400;600&display=swap" rel="stylesheet">
<style>
  :root {
    --backdrop: #222222;
    --card-blue: #1277c4;
    --brand-light: #4a9be0;
    --brand-blue: #1a7fd4;
    --card-dark: #1f1f23;
    --text-light: #ffffff;
    --shadow: rgba(0, 0, 0, 0.55);
  }
  * { box-sizing: border-box; margin: 0; padding: 0; }
  html, body {
    width: 1200px; height: 780px; overflow: hidden;
    background: var(--backdrop);
  }
  .canvas { position: relative; width: 1200px; height: 780px; }

  .card {
    position: absolute; width: 560px; height: 320px;
    box-shadow: 0 14px 30px var(--shadow);
    overflow: hidden;
  }

  /* Front */
  .card-front {
    left: 60px; top: 70px;
    background: var(--card-blue);
    display: flex; align-items: center; justify-content: center;
  }
  .brand-name {
    display: flex; align-items: center; gap: 14px;
    font-family: "Montserrat", sans-serif; font-weight: 700;
    letter-spacing: 1px;
  }
  .card-front .brand-name { font-size: 38px; color: var(--brand-light); }
  .brand-mark { width: 26px; height: 26px; background: currentColor; }

  /* Back */
  .card-back {
    left: 580px; top: 400px;
    background: var(--card-dark);
    font-family: "Open Sans", sans-serif; color: var(--text-light);
  }
  .person {
    position: absolute; right: 34px; top: 30px; text-align: right;
  }
  .person-name {
    font-family: "Montserrat", sans-serif; font-weight: 700;
    font-size: 32px; line-height: 1; color: var(--brand-blue);
  }
  .person-title { font-size: 14px; font-weight: 600; margin-top: 6px; }
  .accent-bar {
    position: absolute; right: 0; top: 26px;
    width: 20px; height: 44px; background: var(--brand-blue);
  }
  .card-back .brand-name {
    position: absolute; left: 40px; top: 118px;
    font-size: 26px; color: var(--brand-blue);
  }
  .card-back .brand-mark { width: 18px; height: 18px; }
  .address {
    position: absolute; left: 40px; top: 196px;
    font-size: 13px; line-height: 1.4;
  }
  .contact-list {
    position: absolute; left: 40px; top: 240px; list-style: none;
    font-size: 13px; line-height: 1.5;
  }
  .contact-list li { display: flex; align-items: center; gap: 8px; }
  .contact-list svg { width: 13px; height: 13px; fill: none; stroke: var(--brand-blue); stroke-width: 2; }
</style>
</head>
<body>
<main class="canvas">
  <section class="card card-front" aria-label="Card front">
    <div class="brand-name"><span class="brand-mark"></span>Tall Fern Roofing</div>
  </section>

  <section class="card card-back" aria-label="Card back">
    <div class="accent-bar"></div>
    <div class="person">
      <div class="person-name">Mark Ellison</div>
      <div class="person-title">Managing Director</div>
    </div>

    <div class="brand-name"><span class="brand-mark"></span>Tall Fern Roofing</div>

    <address class="address" style="font-style:normal">
      1840 Cedar Ridge Ave. Suite 310<br>
      Maple Falls, TX 75010
    </address>

    <ul class="contact-list">
      <li>
        <svg viewBox="0 0 24 24" aria-hidden="true"><path d="M5 3h4l2 5-3 2a12 12 0 0 0 6 6l2-3 5 2v4a2 2 0 0 1-2 2A18 18 0 0 1 3 5a2 2 0 0 1 2-2z"/></svg>
        (555) 214-6093
      </li>
      <li>
        <svg viewBox="0 0 24 24" aria-hidden="true"><rect x="3" y="5" width="18" height="14"/><path d="M3 6l9 7 9-7"/></svg>
        info@website.com
      </li>
      <li>
        <svg viewBox="0 0 24 24" aria-hidden="true"><circle cx="12" cy="12" r="9"/><path d="M3 12h18M12 3a14 14 0 0 1 0 18M12 3a14 14 0 0 0 0 18"/></svg>
        www.website.com
      </li>
    </ul>
  </section>
</main>
</body>
</html>
```